Business card design for holistic health care clinic

We need a double-sided business card design for our holistic health care clinic that integrates our logo design and also its color scheme. My business is called Valmira. It is an integrative medicine clinic. You have already done the logo for me. Please ensure an elegant and upscale design that is not cluttered, but still has all the necessary information (please see below for details).

Target Market(s)

Wellness, fitness, rehabilitation for educated, well-traveled open-minded clients who are focused on natural, organic, balanced and preventive healthcare and lifestyle.

Industry/Entity Type

Medical

Contact Information for Business Card

Modern, clean.

Number of Pages Required

1 page

Font styles to use
Serif
Sans Serif

Colors

Designer to choose colors to be used in the design.

Requirements
Must have
• Logo on one side, all other information on the other side.
• Other information should include:
• Tobias Wrenfeld - DOE, CPT, LMT
• 4100 East Marrow Drive
• Austin, TX 78119
• 512 555 0148
• 818 555 0192
• info@ValmiraHealth.example
• t.wrenfeld@ValmiraHealth.example
Nice to have
• Darker background on front - but not totally black - shaded/dark gray.

```html
<!DOCTYPE html>
<html lang="en">
<head>
<meta charset="utf-8">
<title>Valmira – Business Card</title>
<link rel="stylesheet" href="https://fonts.googleapis.com/css2?family=Montserrat:wght@700&family=Open+Sans:wght@400;600&display=swap">
<style>
  :root {
    --clinic-blue: #1a94d2;
    --clinic-blue-deep: #0f86c6;
    --swoosh-gray: #3a3b3d;
    --ink: #2b2b2b;
    --card-white: #ffffff;
    --page-bg: #ecebe8;
  }
  * { box-sizing: border-box; margin: 0; padding: 0; }
  html, body {
    width: 1200px; height: 900px; overflow: hidden;
    background: var(--page-bg);
  }
  .canvas {
    position: relative; width: 1200px; height: 900px;
    display: flex; flex-direction: column; align-items: center; justify-content: center;
    gap: 40px;
  }
  .card {
    position: relative; width: 640px; height: 366px; overflow: hidden;
    box-shadow: 0 6px 18px rgba(0,0,0,0.18);
  }
  /* Front side */
  .card--front {
    background: var(--clinic-blue);
    display: flex; align-items: center; justify-content: center;
  }
  .brand {
    display: flex; align-items: center; gap: 14px;
    font-family: "Montserrat", sans-serif; font-weight: 700;
    letter-spacing: 1px;
  }
  .brand__dot {
    width: 18px; height: 18px; border-radius: 50%;
    background: currentColor;
  }
  .card--front .brand { color: var(--card-white); font-size: 64px; }
  /* Back side */
  .card--back { background: var(--card-white); }
  .card__waves { position: absolute; inset: 0; width: 640px; height: 366px; }
  .holder {
    position: absolute; left: 40px; top: 58px;
    display: flex; align-items: baseline; gap: 10px;
  }
  .holder__name {
    font-family: "Montserrat", sans-serif; font-weight: 700;
    font-size: 19px; color: var(--clinic-blue-deep); letter-spacing: 0.5px;
  }
  .holder__credentials {
    font-family: "Open Sans", sans-serif; font-size: 12px; color: var(--ink);
  }
  .card--back .brand {
    position: absolute; right: 36px; top: 52px;
    color: var(--clinic-blue); font-size: 42px; gap: 10px;
  }
  .card--back .brand__dot { width: 12px; height: 12px; }
  .contacts {
    position: absolute; left: 40px; top: 176px;
    list-style: none;
    font-family: "Open Sans", sans-serif; font-size: 15px; color: var(--ink);
    line-height: 22px;
  }
  .contacts li { display: flex; align-items: center; gap: 8px; }
  .contacts svg { width: 13px; height: 13px; fill: var(--clinic-blue-deep); flex: none; }
  .address {
    position: absolute; right: 30px; bottom: 84px;
    font-family: "Open Sans", sans-serif; font-size: 13px; color: var(--card-white);
  }
</style>
</head>
<body>
<main class="canvas">

  <section class="card card--front" aria-label="Card front">
    <div class="brand"><span class="brand__dot"></span><span>VALMIRA</span></div>
  </section>

  <section class="card card--back" aria-label="Card back">
    <svg class="card__waves" viewBox="0 0 640 366" aria-hidden="true">
      <path d="M0,366 L0,344 C170,366 330,318 450,240 C520,196 585,176 640,170 L640,366 Z" fill="var(--clinic-blue)"/>
      <path d="M60,318 C210,346 340,296 455,222 C520,182 570,166 600,160 C560,178 510,200 460,238 C340,318 210,352 60,318 Z" fill="var(--swoosh-gray)"/>
    </svg>

    <div class="holder">
      <span class="holder__name">TOBIAS WRENFELD</span>
      <span class="holder__credentials">DOE, CPT, LMT</span>
    </div>

    <div class="brand"><span class="brand__dot"></span><span>VALMIRA</span></div>

    <ul class="contacts">
      <li><svg viewBox="0 0 16 16"><path d="M3 1h3l1.5 4-2 1.5a9 9 0 0 0 4 4L11 8.5l4 1.5v3a2 2 0 0 1-2 2A12 12 0 0 1 1 3a2 2 0 0 1 2-2z"/></svg>512 555 0148</li>
      <li><svg viewBox="0 0 16 16"><path d="M4 0h8a1 1 0 0 1 1 1v14a1 1 0 0 1-1 1H4a1 1 0 0 1-1-1V1a1 1 0 0 1 1-1zm1 2v10h6V2zm3 11a1 1 0 1 0 0 2 1 1 0 0 0 0-2z"/></svg>818 555 0192</li>
      <li><svg viewBox="0 0 16 16"><path d="M0 3h16v10H0zm1.5 1.2v.4L8 9l6.5-4.4v-.4z"/></svg>info@ValmiraHealth.example</li>
      <li><svg viewBox="0 0 16 16"><path d="M0 3h16v10H0zm1.5 1.2v.4L8 9l6.5-4.4v-.4z"/></svg>t.wrenfeld@ValmiraHealth.example</li>
      <li><svg viewBox="0 0 16 16"><circle cx="8" cy="8" r="7.5"/></svg>www.ValmiraHealth.example</li>
    </ul>

    <p class="address">4100 East Marrow Drive Austin, TX 78119</p>
  </section>

</main>
</body>
</html>
```